New Zealand Marlborough Sauvignon Blanc wine packaging design

We need packaging design for our new wine brand, Dunmore Vale. The wine is a New Zealand Marlborough Sauvignon Blanc. We would like the packaging will portray elegance and style with an understated label. We are looking for a label that portrays the elegance of the French Riviera. The label should be round or pill shaped.
Updates

Industry/Entity Type

Wine

Font styles to use
Serif
Sans Serif

Requirements
Must have
• The words in order of importance: Dunmore Vale, Sauvignon Blanc, Marlborough, New Zealand. It should be fit to the bottle posted in the links
Nice to have
• a pill shape or circular shape
Should not have
• Illustrations of wine bottles, wine glasses, or grapes

```html
<!DOCTYPE html>
<html lang="en">
<head>
<meta charset="utf-8">
<title>Dunmore Vale Sauvignon Blanc Label</title>
<link rel="stylesheet" href="https://fonts.googleapis.com/css2?family=Cormorant+Garamond:wght@400;500&family=Italiana&family=Monsieur+La+Doulaise&display=swap">
<style>
  :root {
    --page: #ffffff;
    --label: #3a4b49;
    --pattern-light: #3e504d;
    --pattern-dark: #334341;
    --ink: #ffffff;
  }
  * { margin: 0; padding: 0; box-sizing: border-box; }
  html, body {
    width: 1200px;
    height: 675px;
    overflow: hidden;
    background: var(--page);
  }
  .canvas {
    position: relative;
    width: 1200px;
    height: 675px;
    background: var(--page);
  }
  .label {
    position: absolute;
    left: 358px;
    top: 95px;
    width: 484px;
    height: 484px;
  }
  .label-art {
    position: absolute;
    inset: 0;
  }
  .brand-mark {
    position: absolute;
    left: 0;
    right: 0;
    top: 120px;
    text-align: center;
    font-family: "Cormorant Garamond", serif;
    font-weight: 400;
    font-size: 15px;
    letter-spacing: 4px;
    text-transform: uppercase;
    color: var(--ink);
  }
  .brand-name {
    position: absolute;
    left: 0;
    right: 0;
    top: 218px;
    text-align: center;
    font-family: "Cormorant Garamond", serif;
    font-weight: 400;
    font-size: 34px;
    line-height: 1;
    letter-spacing: 11px;
    padding-left: 11px;
    text-transform: uppercase;
    color: var(--ink);
  }
  .varietal {
    position: absolute;
    left: 0;
    right: 0;
    top: 248px;
    text-align: center;
    font-family: "Monsieur La Doulaise", cursive;
    font-size: 40px;
    line-height: 1;
    color: var(--ink);
  }
  .region {
    position: absolute;
    left: 129px;
    top: 350px;
    width: 226px;
    height: 33px;
    border: 1px solid var(--ink);
    display: flex;
    align-items: center;
    justify-content: center;
    font-family: "Italiana", serif;
    font-size: 12.5px;
    letter-spacing: 0.3px;
    text-transform: uppercase;
    color: var(--ink);
  }
</style>
</head>
<body>
  <main class="canvas">
    <section class="label">
      <svg class="label-art" width="484" height="484" viewBox="0 0 484 484">
        <defs>
          <radialGradient id="pattern-tone" cx="50%" cy="50%" r="50%">
            <stop offset="0%" stop-color="var(--pattern-light)"/>
            <stop offset="100%" stop-color="var(--pattern-dark)"/>
          </radialGradient>
        </defs>
        <circle class="label-disc" cx="242" cy="242" r="242" fill="var(--label)"/>
        <circle class="label-ornament" cx="242" cy="242" r="222" fill="url(#pattern-tone)" opacity="0.6"
                role="img" aria-label="Faint tonal ornamental koru and woven pattern behind the label text"/>
        <circle class="label-ring" cx="242" cy="242" r="200" fill="none" stroke="var(--ink)" stroke-width="0.6"/>
      </svg>
      <div class="brand-mark">Dunmore Vale</div>
      <h1 class="brand-name">Dunmore Vale</h1>
      <p class="varietal">Sauvignon Blanc</p>
      <p class="region">Marlborough, New Zealand</p>
    </section>
  </main>
</body>
</html>
```